Brenton's Insurance Servives, Inc.

Full Service Insurance Broker.
Senior Health Care, Life, Annuity, Auto and Home
Specializing in Medicare Supplements. No cost, No Obligation Consulting.

Target Market(s)

General Public and senior citizens

Industry/Entity Type

Insurance Broker

Font styles to use
Decorative
Script

```html
<!DOCTYPE html>
<html lang="en">
<head>
<meta charset="utf-8">
<title>Brenton's Insurance Servives, Inc. – Medicare Supplements Banner</title>
<link href="https://fonts.googleapis.com/css2?family=Great+Vibes&family=Montserrat:wght@400;500;600;700;800&display=swap" rel="stylesheet">
<style>
  :root{
    --page:#e4e4e4;
    --white:#ffffff;
    --brand-blue:#1580c3;
    --script-blue:#1a7bc4;
    --navy:#27285f;
    --ink:#1c1c1c;
    --cyan:#1da1e6;
    --link-blue:#1a8fd6;
    --icon-navy:#2b2e6e;
  }
  *{margin:0;padding:0;box-sizing:border-box}
  html,body{width:1200px;height:733px;overflow:hidden;background:var(--page)}
  .banner{position:absolute;left:0;top:66px;width:1200px;height:600px;background:var(--white);overflow:hidden;font-family:"Montserrat",sans-serif}
  .scene-photo{position:absolute;left:560px;top:0;width:640px;height:600px;
    background:linear-gradient(90deg,#ffffff 0%,rgba(255,255,255,0) 22%),
               linear-gradient(180deg,#e9eef0 0%,#cfd9c9 35%,#e8d6cf 60%,#d9dde4 100%)}
  .company-name{position:absolute;left:150px;top:52px;width:300px;text-align:center;
    font-weight:700;font-size:17px;color:var(--navy);line-height:1.25}
  .headline-script{position:absolute;left:98px;top:96px;font-family:"Great Vibes",cursive;
    font-size:108px;line-height:1;color:var(--script-blue);white-space:nowrap}
  .headline-sub{position:absolute;left:172px;top:196px;width:280px;font-weight:800;
    font-size:34px;line-height:1;color:var(--ink)}
  .headline-sub span{display:block}
  .headline-sub .line-one{padding-left:20px}
  .swoosh{position:absolute;left:225px;top:262px}
  .benefits{position:absolute;left:50px;top:305px;display:flex;align-items:center;gap:8px;
    font-size:23px;font-weight:500;color:var(--ink);white-space:nowrap}
  .benefits svg{flex:none}
  .service-band{position:absolute;left:20px;top:351px;width:581px;height:156px;
    background:var(--brand-blue);border-radius:78px 78px 0 0 / 78px 78px 0 0;
    display:flex;justify-content:space-between;padding:0 20px 0 22px}
  .service{position:relative;width:100px;display:flex;flex-direction:column;align-items:center}
  .service-icon{width:82px;height:82px;border-radius:50%;background:var(--white);margin-top:13px;
    display:flex;align-items:center;justify-content:center}
  .service-label{color:var(--white);font-weight:600;font-size:16px;text-align:center;
    line-height:1.15;margin-top:auto;margin-bottom:22px}
  .service-divider{width:1.5px;height:90px;background:rgba(255,255,255,.7);align-self:flex-end;margin-bottom:20px}
  .call-bar{position:absolute;left:17px;top:497px;width:585px;height:50px;background:var(--navy);
    border-radius:25px;display:flex;align-items:center;justify-content:center;
    font-weight:800;font-size:26px;color:var(--white);white-space:nowrap;letter-spacing:-.2px}
  .call-bar .call-label{color:var(--cyan);margin-right:8px}
  .contact-line{position:absolute;left:36px;top:556px;display:flex;align-items:center;gap:6px;white-space:nowrap}
  .contact-name{font-weight:800;font-size:27px;color:var(--navy);margin-right:6px}
  .contact-item{font-weight:500;font-size:19px;color:var(--link-blue);letter-spacing:1.5px}
  .contact-sep{font-size:20px;color:var(--navy)}
</style>
</head>
<body>
<main class="banner">
  <div class="scene-photo" role="img" aria-label="Photo: a smiling senior woman seated on a sofa talking with a young caregiver by a bright window"></div>

  <div class="company-name">Brenton's Insurance Servives, Inc.</div>

  <div class="headline-script">Specializing</div>
  <h1 class="headline-sub"><span class="line-one">in Medicare</span><span>Supplements.</span></h1>
  <svg class="swoosh" width="150" height="30" viewBox="0 0 150 30" aria-hidden="true">
    <path d="M2 28 C40 10 100 2 148 6" fill="none" stroke="var(--ink)" stroke-width="2"/>
  </svg>

  <p class="benefits">
    <svg width="34" height="30" viewBox="0 0 34 30" aria-hidden="true"><rect x="2" y="4" width="24" height="24" rx="9" fill="none" stroke="var(--script-blue)" stroke-width="2.5"/><path d="M8 15 l6 7 L32 2" fill="none" stroke="var(--script-blue)" stroke-width="3.5" stroke-linecap="round" stroke-linejoin="round"/></svg>
    <span>No cost,</span>
    <svg width="34" height="30" viewBox="0 0 34 30" aria-hidden="true" style="margin-left:6px"><rect x="2" y="4" width="24" height="24" rx="9" fill="none" stroke="var(--script-blue)" stroke-width="2.5"/><path d="M8 15 l6 7 L32 2" fill="none" stroke="var(--script-blue)" stroke-width="3.5" stroke-linecap="round" stroke-linejoin="round"/></svg>
    <span>No Obligation Consulting.</span>
  </p>

  <section class="service-band">
    <div class="service">
      <div class="service-icon">
        <svg width="50" height="50" viewBox="0 0 50 50" fill="none" stroke="var(--icon-navy)" stroke-width="2.5" stroke-linecap="round" aria-hidden="true"><path d="M10 6 v14 a10 10 0 0 0 20 0 V6"/><path d="M20 30 v6 a8 8 0 0 0 16 0 v-4"/><circle cx="36" cy="27" r="5"/><circle cx="36" cy="27" r="1.5"/></svg>
      </div>
      <span class="service-label">Senior<br>Health Care</span>
    </div>
    <span class="service-divider"></span>
    <div class="service">
      <div class="service-icon">
        <svg width="50" height="50" viewBox="0 0 50 50" fill="none" stroke="var(--icon-navy)" stroke-width="2.3" stroke-linejoin="round" aria-hidden="true"><path d="M25 30 C14 22 12 16 16 12 c3-3 7-2 9 1 c2-3 6-4 9-1 c4 4 2 10-9 18z"/><path d="M25 14 v8 M21 18 h8"/><path d="M6 22 l4 14 8 8 M44 22 l-4 14 -8 8"/></svg>
      </div>
      <span class="service-label">Life</span>
    </div>
    <span class="service-divider"></span>
    <div class="service">
      <div class="service-icon">
        <svg width="52" height="52" viewBox="0 0 52 52" fill="none" stroke="var(--icon-navy)" stroke-width="2.3" aria-hidden="true"><rect x="5" y="8" width="30" height="28" rx="2"/><path d="M5 15 h30 M12 5 v6 M28 5 v6 M11 21 h4 M18 21 h4 M25 21 h4 M11 27 h4 M18 27 h4"/><circle cx="37" cy="36" r="10"/><path d="M37 30 v12 M34 33 h5 a2 2 0 0 1 0 4 h-3 a2 2 0 0 0 0 4 h5"/></svg>
      </div>
      <span class="service-label">Annuity</span>
    </div>
    <span class="service-divider"></span>
    <div class="service">
      <div class="service-icon">
        <svg width="54" height="44" viewBox="0 0 54 44" fill="none" stroke="var(--icon-navy)" stroke-width="2.5" stroke-linejoin="round" aria-hidden="true"><path d="M10 18 l5-11 h24 l5 11"/><rect x="5" y="18" width="44" height="14" rx="3"/><path d="M9 32 v6 h7 v-6 M38 32 v6 h7 v-6"/><circle cx="13" cy="25" r="2.5"/><circle cx="41" cy="25" r="2.5"/><path d="M21 25 h12"/></svg>
      </div>
      <span class="service-label">Auto</span>
    </div>
    <span class="service-divider"></span>
    <div class="service">
      <div class="service-icon">
        <svg width="54" height="50" viewBox="0 0 54 50" fill="none" stroke="var(--icon-navy)" stroke-width="2.3" stroke-linejoin="round" aria-hidden="true"><path d="M4 22 L27 6 L50 22"/><path d="M9 19 v25 h36 V19"/><rect x="22" y="30" width="10" height="14"/><rect x="13" y="26" width="6" height="6"/><rect x="35" y="26" width="6" height="6"/><rect x="24" y="16" width="6" height="6"/></svg>
      </div>
      <span class="service-label">Home</span>
    </div>
  </section>

  <div class="call-bar"><span class="call-label">Call us:</span>1-800-555-0142 and 412-555-0187</div>

  <div class="contact-line">
    <span class="contact-name">Dale</span>
    <svg width="20" height="20" viewBox="0 0 20 20" aria-hidden="true"><circle cx="10" cy="10" r="8.5" fill="none" stroke="var(--navy)" stroke-width="1.6"/><path d="M6.5 5.5 l2 2 -1 1.5 c1 2 2 3 4 4 l1.5-1 2 2 -1.5 1.5 c-4 0-8-4-8-8z" fill="var(--navy)"/></svg>
    <span class="contact-item">412-555-0163</span>
    <span class="contact-sep">|</span>
    <svg width="20" height="20" viewBox="0 0 20 20" fill="none" stroke="var(--navy)" stroke-width="1.5" aria-hidden="true"><circle cx="10" cy="10" r="8.5"/><ellipse cx="10" cy="10" rx="3.5" ry="8.5"/><path d="M1.5 10 h17 M3 5.5 h14 M3 14.5 h14"/></svg>
    <span class="contact-item">www.brenton-ins.com</span>
  </div>
</main>
</body>
</html>
```